Executive recruiting firm in need of business card design

Executive recruiting firm looking for a sleek, classy and modern business card design; card itself will be square shape, rounded edges and soft touch paper, our colors are dark blues in the navy color scale, silvers and grays. Reference our website for a better idea of our company's feel and goals at Tarvex-Up.com - our company message is "Employee Engagement Begins at Recruitment" this should be on the card

```html
<!DOCTYPE html>
<html lang="en">
<head>
<meta charset="utf-8">
<title>Tarvex Up — Business Card</title>
<link rel="stylesheet" href="https://fonts.googleapis.com/css2?family=Open+Sans:wght@400;700&display=swap">
<style>
  :root {
    --navy: #161a47;
    --paper: #f7f7f6;
    --backdrop: #e9eaec;
    --ink: #1b1f4d;
    --silver: #c4c7d2;
    --white: #ffffff;
  }
  * { margin: 0; padding: 0; box-sizing: border-box; }
  html, body {
    width: 1200px; height: 900px; overflow: hidden;
    background: var(--backdrop);
    font-family: "Open Sans", Arial, sans-serif;
  }
  .sheet {
    width: 1200px; height: 900px;
    display: flex; align-items: center; justify-content: center; gap: 60px;
  }
  .card {
    position: relative;
    width: 400px; height: 400px;
    border-radius: 22px;
    box-shadow: 0 2px 8px rgba(0,0,0,0.12);
  }
  .card--front { background: var(--paper); color: var(--ink); }
  .card--back  { background: var(--navy); color: var(--white); }

  .holder { position: absolute; left: 36px; top: 36px; }
  .holder__name { font-weight: 700; font-size: 15px; letter-spacing: 0.3px; }
  .holder__role { font-size: 12px; margin-top: 2px; }

  .brand {
    position: absolute; left: 0; right: 0; top: 150px;
    text-align: center;
  }
  .brand__name { font-weight: 700; font-size: 30px; line-height: 1.1; }
  .brand__message { font-size: 12px; margin-top: 10px; }
  .card--back .brand { top: 165px; }
  .card--back .brand__message { color: var(--silver); }

  .contacts { position: absolute; left: 36px; bottom: 36px; list-style: none; }
  .contacts li { display: flex; align-items: center; gap: 7px; font-size: 12px; line-height: 19px; }
  .contacts svg { width: 9px; height: 9px; fill: var(--ink); flex: none; }

  .address {
    position: absolute; right: 36px; bottom: 36px;
    text-align: right; font-size: 12px; line-height: 19px;
  }
</style>
</head>
<body>
<main class="sheet">
  <section class="card card--front" aria-label="Card front">
    <div class="holder">
      <p class="holder__name">MARCUS ELLERY</p>
      <p class="holder__role">Managing Director</p>
    </div>
    <div class="brand">
      <p class="brand__name">TARVEX UP</p>
      <p class="brand__message">Employee Engagement Begins at Recruitment</p>
    </div>
    <ul class="contacts">
      <li><svg viewBox="0 0 10 10"><path d="M2 0.5 L3.6 2.6 L2.7 3.6 Q3.6 5.8 6.3 7.3 L7.4 6.4 L9.5 8 L8.2 9.5 Q2.5 8.5 0.5 1.8 Z"/></svg>(044)555019284</li>
      <li><svg viewBox="0 0 10 10"><rect x="0.5" y="2" width="9" height="6.5" rx="0.8"/></svg>info@tarvexmail.com</li>
      <li><svg viewBox="0 0 10 10"><circle cx="5" cy="5" r="4.5"/></svg>www.Tarvex-Up.com</li>
    </ul>
    <p class="address">4821, Harlow Street,<br>Brenmoor, 56073</p>
  </section>

  <section class="card card--back" aria-label="Card back">
    <div class="brand">
      <p class="brand__name">TARVEX UP</p>
      <p class="brand__message">Employee Engagement Begins at Recruitment</p>
    </div>
  </section>
</main>
</body>
</html>
```